Professional BIO Template with photo and logo

Hello,
I need a professional Bio template developed via Microsoft WORD ASAP!!!!! I would like to just be able to add the text I need to add. So resize-able text boxes. Potentially able to adjust the font. These are the things I need added it to include.
Head shot (attached)
Text Box for Name
Text Box for phone number
Text box for email
KVT Logo (attached)
Maybe a blue banner at the top or some background boxes that are blue or grey. Here are the pantone colors that our company uses.

CORE COLOR
100c 91m 17y 6k 38r 58g 128b Hex #263A80 Pantone 7687 C

CORE CONTRAST COLOR
36c 29m 28y 0k 168r 168g 170b Hex #669999 Pantone Cool Gray 6C

I also attached some examples of what we have been looking at. Instead of green add the blue...instead of black maybe just be white.

Thank you

```html
<!DOCTYPE html>
<html lang="en">
<head>
<meta charset="UTF-8">
<title>Dan Harlow – Bio</title>
<link rel="stylesheet" href="https://fonts.googleapis.com/css2?family=Carlito:wght@400;700&family=Lato:wght@900&display=swap">
<style>
  :root {
    --core-blue: #263A80;
    --contrast-teal: #669999;
    --ink: #111111;
    --white: #ffffff;
    --photo-dark: #2a2a2c;
    --photo-mid: #6a6b6e;
  }
  * { margin: 0; padding: 0; box-sizing: border-box; }
  html, body { width: 848px; height: 1200px; overflow: hidden; background: var(--white); }
  .bio-page {
    position: relative;
    width: 848px;
    height: 1200px;
    overflow: hidden;
    font-family: "Carlito", Calibri, Arial, sans-serif;
    color: var(--ink);
    background: var(--white);
  }
  .header-band {
    position: absolute; left: 0; top: 0;
    width: 848px; height: 455px;
    background: var(--core-blue);
  }
  .name {
    position: absolute; left: 38px; top: 56px;
    color: var(--white);
    font-family: "Lato", Arial, sans-serif;
    font-weight: 900;
    font-size: 96px;
    line-height: 92px;
    letter-spacing: 5px;
    text-transform: uppercase;
  }
  .job-title {
    position: absolute; left: 40px; top: 250px;
    color: var(--white);
    font-weight: 700;
    font-size: 38px;
    line-height: 44px;
    letter-spacing: 0.3px;
  }
  .contact {
    position: absolute; left: 41px;
    color: var(--white);
    font-weight: 700;
    font-size: 25px;
    line-height: 30px;
    letter-spacing: 0.6px;
  }
  .contact.email { top: 306px; }
  .contact.phone { top: 354px; font-size: 27px; }
  .headshot-frame {
    position: absolute; left: 515px; top: 215px;
    width: 292px; height: 447px;
    background: var(--white);
    padding: 4px;
  }
  .headshot {
    width: 100%; height: 100%;
    background: radial-gradient(ellipse at 50% 35%, var(--photo-mid) 0%, var(--photo-dark) 75%);
  }
  .section-head {
    position: absolute; left: 0; top: 496px;
    width: 519px; height: 46px;
    display: flex; align-items: center; gap: 10px;
  }
  .section-bar {
    height: 34px;
    background: var(--contrast-teal);
  }
  .section-bar.lead { width: 26px; flex: none; }
  .section-bar.trail { flex: 1; }
  .section-title {
    flex: none;
    font-weight: 700;
    font-size: 44px;
    line-height: 46px;
    letter-spacing: 0.5px;
  }
  .about-text {
    position: absolute; left: 37px;
    font-size: 17.5px;
    line-height: 28px;
    text-align: justify;
    text-align-last: left;
  }
  .about-text.p1 { top: 556px; width: 420px; }
  .about-text.p2 { top: 690px; width: 758px; }
  .about-text.p3 { top: 794px; width: 758px; }
  .about-text.p4 { top: 898px; width: 420px; }
  .company-mark {
    position: absolute; left: 545px; top: 919px;
    width: 233px; height: 171px;
    display: flex; align-items: center; justify-content: center; gap: 12px;
    color: var(--core-blue);
    font-weight: 700;
    font-size: 56px;
    letter-spacing: 4px;
  }
  .company-mark .mark-square {
    width: 26px; height: 26px;
    background: var(--core-blue);
  }
</style>
</head>
<body>
  <main class="bio-page">
    <header class="header-band"></header>
    <h1 class="name">Dan<br>Harlow</h1>
    <p class="job-title">LSOIEKAWSE LSIENK</p>
    <p class="contact email">dan.harlow@mail.com</p>
    <p class="contact phone">(555) 214.7730</p>

    <div class="headshot-frame">
      <div class="headshot" role="img" aria-label="Head shot portrait of Dan Harlow in a dark blazer and white shirt"></div>
    </div>

    <div class="section-head">
      <span class="section-bar lead"></span>
      <h2 class="section-title">ABOUT</h2>
      <span class="section-bar trail"></span>
    </div>

    <p class="about-text p1">Perspiciatis unde omnis iste natus error sit voluptatem accusantium doloremque laudantium, totam rem aperiam, eaque ipsa quae ab illo inventore veritatis et quasi architecto beatae vitae dicta sunt explicabo.</p>
    <p class="about-text p2">Nemo enim ipsam voluptatem quia voluptas sit aspernatur aut odit aut fugit, sed quia consequuntur magni dolores eos qui ratione voluptatem sequi nesciunt. Neque porro quisquam est, qui dolorem ipsum quia dolor sit amet, consectetur, adipisci velit, sed quia non numquam eius modi tempora incidunt ut</p>
    <p class="about-text p3">Liseon quia voluptas sit aspernatur aut odit aut fugit, sed quia consequuntur magni dolores eos qui ratione voluptatem sequi nesciuntorro quisquam est, qui dolorem ipsum quia dolor sit amet, consectetur, adipisci velit, sed quia non numquam eius modi tempora incidunt.</p>
    <p class="about-text p4">Perspiciatis unde omnis iste natus error sit voluptatem accusantium doloremque laudantium, totam rem aperiam, eaque ipsa quae ab illo inventore veritatis et quasi architecto beatae vitae dicta sunt explicabo. Nemo enim ipsam voluptatem quia voluptas sit aspernatur aut odit aut fugit, sed quia consequuntur magni dolores eos qui ratione voluptatem sequi nesciunt. Neque porro quisquam est, qui dolorem ipsum quia dolor sit amet, consectetur, adipisci velit, sed quia non numquam eius modi.</p>

    <div class="company-mark">
      <span class="mark-square"></span>
      <span class="mark-name">KVT</span>
    </div>
  </main>
</body>
</html>
```